Financial investment calculator report for real estae - layout & design

I am looking to Create a web report utilizing the attached information. It is an investment calculator report that will be customized report based on an online calculator. Therefore the report will need to be designed in a manner that a backend developer will be able to build off of.

The report will need to be web based but also printed in PDF format. The report will need to include the calculation format as well as be templeted to add a report user unique profile information like Headshot, Business Logo, Name, Telephone number, email etc.

The report should be modern and clean and easy to read and use a modern clean template design. It should be able to be easily color customized by the end user to produce templets in Red, Blue, Green, and Greyscale.

The report should be no more than 3 pages total with out breaking up the sections.

Section One - Cover sheet including agent bio info, Report Title and property address (both prominent), 400 Character space for property description, Property Pictures (3), and a google Maps integration image showing property location, It should also have room for about 100 words for a text disclaimer. (I will provide text soon)

Section Two - Inputs from the calculator

Section 3 - The Four Benefits & Rates of Return

Once I have a completed/approved form I will have about a half dozen forms/reports that will need to be laid out with a similar aesthetic.

Feel free to ask me any questions. Thank You
Milo

Target Market(s)

This report will be produced by real estate agents forvtheir investor clients. It should denote professionalism

Font styles to use
Sans Serif

Colors
0054AA
0677BA
7BADD7
CADEEF
E8F1F8
00AB8E
00BBA5
67D7C9
C6EFE9
E9F9F6
EB3D1F
EC4F4E
F09395
F8D3D4
FCEDEE

```html
<!DOCTYPE html>
<html lang="en">
<head>
<meta charset="utf-8">
<title>Investment Analysis Report – 418 Alder</title>
<link href="https://fonts.googleapis.com/css2?family=Lato:wght@300;400;700;900&display=swap" rel="stylesheet">
<style>
:root{
  --accent:#2b1fe3;
  --ink:#111111;
  --muted:#555555;
  --rule:#e2e2e2;
  --band:#f0f0f0;
  --paper:#ffffff;
  --backdrop:#edf5fc;
  --neg:#e5485d;
}
*{box-sizing:border-box;margin:0;padding:0}
html,body{width:1200px;height:1012px;overflow:hidden}
body{background:var(--backdrop);font-family:'Lato',sans-serif;color:var(--ink);position:relative}
.page{position:absolute;top:244px;width:370px;height:524px;background:var(--paper);box-shadow:0 10px 28px rgba(60,80,110,.18)}
.page-1{left:30px}.page-2{left:415px}.page-3{left:800px}
.abs{position:absolute}
.logo-mark{border-radius:50%;background:#000}
.agency{font-size:7px;letter-spacing:.1px;white-space:nowrap}
.agency b{font-weight:700}.agency span{font-weight:300;color:#444}
.agent{text-align:right;font-size:3.6px;line-height:8.6px;color:var(--ink)}
.agent-name{font-size:6.6px;color:var(--accent);font-weight:900;line-height:8px}
.agent-name span{font-weight:300}
.agent svg{width:4px;height:4px;vertical-align:-0.5px;margin-right:6px}
.headshot{background:linear-gradient(160deg,#8fb0b8,#5b6f5e 55%,#2d4a34);border-radius:2px}
.doc-title{font-size:13px;white-space:nowrap}
.doc-title b{font-weight:700}.doc-title span{font-weight:300}
.rule{height:1px;background:var(--rule)}
.rule-accent{height:1.3px;background:var(--accent)}
.photo{border-radius:3px;box-shadow:0 1px 3px rgba(0,0,0,.2)}
.ph-a{background:linear-gradient(180deg,#4a67b8 0%,#d9dde8 45%,#8a7c6c 100%)}
.ph-b{background:linear-gradient(135deg,#5a4434 0%,#2c3f8a 40%,#4bb6e8 60%,#5a3c2a 100%)}
.ph-c{background:linear-gradient(180deg,#3e5fa8 0%,#7b7890 50%,#6e6158 100%)}
.map{background:linear-gradient(90deg,#e9ece8 0%,#e4e7e2 70%,#9fc0f2 80%,#9cbdf0 100%);border-radius:3px}
.prop-title{font-size:10px;font-weight:700;white-space:nowrap}
.prop-sub{font-size:3.5px;font-weight:700}
.prop-desc{font-size:2.9px;line-height:4.85px;color:#555}
.prop-addr{font-size:3.6px;font-weight:700;white-space:nowrap}
.prop-addr svg{width:3.5px;height:4px;vertical-align:-0.6px;margin-right:3px}
.price{display:flex;justify-content:space-between;align-items:baseline;font-size:4.6px;font-weight:700}
.price strong{font-size:6.4px;color:var(--accent);font-weight:400}
.disclaimer h3{font-size:4.6px;font-weight:700;margin-bottom:4px}
.disclaimer p{font-size:2.8px;line-height:4.3px;color:#555}
.footer{font-size:2.9px;color:#555;display:flex;justify-content:space-between;white-space:nowrap}
.section-title{font-size:7.4px;color:var(--accent);white-space:nowrap}
.section-title b{font-weight:700}.section-title span{font-weight:300}
.panel{background:var(--paper);border:1px solid #e4e4e4;border-radius:3px;box-shadow:0 1px 4px rgba(0,0,0,.12);padding:4px 8px 4px}
.sec{display:flex;justify-content:space-between;align-items:center;background:var(--band);height:11px;padding:0 6px 0 4px;font-size:4.4px;font-weight:700;margin-top:2px}
.sec::before{content:"";width:1.8px;height:1.8px;border-radius:50%;background:var(--accent);margin-right:6px;flex:none}
.sec .sec-name{flex:1}
.sec .sec-note{font-size:2.8px;font-weight:400}
.sec.cols{display:grid;grid-template-columns:7.8px 148.2px 86px 40px 1fr;justify-items:start}
.sec.cols::before{margin:0}
.sec.cols em{font-style:normal;font-size:2.8px;font-weight:400}
.row,.total{display:grid;grid-template-columns:77px 62px 86px 40px 1fr;padding-left:17px;align-items:center}
.row{height:7.8px;font-size:2.8px;color:#444;border-bottom:.5px solid var(--rule)}
.row .v{grid-column:5;text-align:right}
.row .neg{color:var(--neg)}
.total{height:9.6px;font-size:4.4px;font-weight:700}
.total .tl{grid-column:3/5;border-top:1.2px solid var(--accent);height:100%;display:flex;align-items:center}
.total .tv{grid-column:5;border-top:1.2px solid var(--accent);height:100%;display:flex;align-items:center;justify-content:flex-end}
.total .lead{grid-column:1}
.total .lead2{grid-column:2}
.sub{font-size:4.2px;font-weight:700;padding:5px 0 2px 17px}
</style>
</head>
<body>

<!-- PAGE 1 : cover -->
<section class="page page-1">
  <div class="abs logo-mark" style="left:17px;top:14px;width:36px;height:36px"></div>
  <div class="abs agency" style="left:59px;top:28px"><b>AGENCYNAME</b> <span>HERE</span></div>
  <div class="abs agent" style="right:90px;top:11px">
    <div class="agent-name">GREG <span>MILO</span></div>
    <div><svg viewBox="0 0 10 10"><path d="M2 1l2 2-1 1.3a6 6 0 0 0 2.7 2.7L7 6l2 2-1.3 1.4C4.5 9.6.4 5.5.6 2.3z" fill="none" stroke="#111" stroke-width="1"/></svg>(555) 014-2290</div>
    <div>greg@agency.test</div>
  </div>
  <div class="abs headshot" role="img" aria-label="Agent headshot" style="left:286px;top:11px;width:56px;height:62px"></div>
  <h1 class="abs doc-title" style="left:16px;top:60px"><b>Investment</b> <span>Analysis:</span></h1>
  <div class="abs rule" style="left:16px;top:78px;width:334px"></div>
  <div class="abs rule-accent" style="left:16px;top:77.5px;width:119px"></div>

  <div class="abs photo ph-a" role="img" aria-label="Property exterior at dusk with courtyard" style="left:16px;top:89px;width:202px;height:112px"></div>
  <div class="abs photo ph-b" role="img" aria-label="Terrace with loungers and pool at night" style="left:17px;top:210px;width:202px;height:112px"></div>
  <div class="abs photo ph-c" role="img" aria-label="Street view of the apartment building at dusk" style="left:17px;top:333px;width:202px;height:112px"></div>

  <h2 class="abs prop-title" style="left:231px;top:88px">418 ALDER</h2>
  <div class="abs prop-sub" style="left:231px;top:101px">15-Plex of 1bd/1bth Apartments</div>
  <p class="abs prop-desc" style="left:231px;top:109px;width:117px">Calm living in this bright 400 sqft apartment. Step into an open room with a neat kitchen and a cozy sofa corner for guests. Rest in the quiet bedroom with a queen bed. Refresh in the clean bathroom with a walk-in shower. Fast internet, smart TV and laundry are included. Enjoy city views from the private balcony, with cafes, shops and parks close by for a relaxed daily routine in town.</p>
  <div class="abs prop-addr" style="left:231px;top:173px"><svg viewBox="0 0 8 10"><path d="M4 0a3.5 3.5 0 0 0-3.5 3.5C.5 6 4 10 4 10s3.5-4 3.5-6.5A3.5 3.5 0 0 0 4 0zm0 5a1.5 1.5 0 1 1 0-3 1.5 1.5 0 0 1 0 3z" fill="#111"/></svg>418 Alder Ave, Fairview, KS 66000</div>
  <div class="abs price" style="left:232px;top:181px;width:112px"><span>PURCHASE PRICE:</span><strong>$1.690.000</strong></div>

  <div class="abs rule" style="left:17px;top:456px;width:333px"></div>
  <div class="abs rule-accent" style="left:17px;top:455.5px;width:118px"></div>
  <div class="abs disclaimer" style="left:17px;top:461px;width:330px">
    <h3>DISCLAIMER:</h3>
    <p>This report is for general information only and is not financial or investment advice. Figures come from sources believed to be sound, yet no warranty is made about their accuracy. Investors should do their own checks and speak with qualified advisors before any purchase decision.</p>
  </div>
  <div class="abs footer" style="left:16px;top:509px;width:334px"><span>418 Alder, REF #47v8487 by Northlake Realty | Report by Lena Ortiz PageForge at www.example-site.test. June 26th, 2023</span><span>Page 1/3</span></div>
</section>

<!-- PAGE 2 : calculator inputs -->
<section class="page page-2">
  <div class="abs logo-mark" style="left:19px;top:7px;width:31px;height:31px"></div>
  <div class="abs agency" style="left:59px;top:18px"><b>AGENCYNAME</b> <span>HERE</span></div>
  <div class="abs agent" style="right:90px;top:12px">
    <div class="agent-name">GREG <span>MILO</span></div>
    <div><svg viewBox="0 0 10 10"><path d="M2 1l2 2-1 1.3a6 6 0 0 0 2.7 2.7L7 6l2 2-1.3 1.4C4.5 9.6.4 5.5.6 2.3z" fill="none" stroke="#111" stroke-width="1"/></svg>(555) 014-2290</div>
    <div>greg@agency.test</div>
  </div>
  <div class="abs headshot" role="img" aria-label="Agent headshot" style="left:295px;top:13px;width:50px;height:53px"></div>
  <div class="abs rule" style="left:16px;top:49px;width:120px;background:var(--accent);height:1.3px"></div>
  <h1 class="abs doc-title" style="left:16px;top:52px"><b>Investment</b> <span>Analysis:</span></h1>

  <div class="abs map" role="img" aria-label="Street map with a marker at the property location" style="left:16px;top:79px;width:150px;height:83px"></div>
  <h2 class="abs prop-title" style="left:179px;top:77px">418 ALDER</h2>
  <div class="abs prop-sub" style="left:179px;top:90px">15-Plex of 1bd/1bth Apartments</div>
  <p class="abs prop-desc" style="left:179px;top:97px;width:170px">Calm living in this bright 400 sqft apartment. Step into an open room with a neat kitchen and a cozy sofa corner for guests. Rest in the quiet bedroom with a queen bed. Refresh in the clean bathroom with a walk-in shower. Fast internet, smart TV and laundry are included. Enjoy city views from the private balcony, with cafes, shops and parks close by.</p>
  <div class="abs prop-addr" style="left:179px;top:157px"><svg viewBox="0 0 8 10"><path d="M4 0a3.5 3.5 0 0 0-3.5 3.5C.5 6 4 10 4 10s3.5-4 3.5-6.5A3.5 3.5 0 0 0 4 0zm0 5a1.5 1.5 0 1 1 0-3 1.5 1.5 0 0 1 0 3z" fill="#111"/></svg>418 Alder Ave, Fairview, KS 66000</div>
  <div class="abs price" style="left:180px;top:164px;width:145px"><span>PURCHASE PRICE:</span><strong>$1.690.000</strong></div>

  <div class="abs panel" style="left:16px;top:177px;width:337px">
    <div class="sec"><span class="sec-name">PROPERTY ADDRESS:</span><span class="sec-note">418 Alder Ave, Fairview, KS 66000</span></div>
    <div class="row"><span>Financing</span><span></span><span>20% Down</span><span></span><span class="v">20 Year Conventional</span></div>
    <div class="row"><span>Purchase Price</span><span></span><span></span><span></span><span class="v">$1.690.000</span></div>
    <div class="row"><span>Down Payment (Cash Invested)</span><span></span><span>20% of purchase price</span><span></span><span class="v">$338.000</span></div>
    <div class="row"><span>Amount Financed</span><span></span><span></span><span></span><span class="v">$1.352.000</span></div>
    <div class="row"><span>Needed Capital Improvements Est</span><span></span><span></span><span></span><span class="v">$0</span></div>
    <div class="row"><span>Est. Closing Costs</span><span></span><span></span><span></span><span class="v">$3.000</span></div>
    <div class="row"><span style="grid-column:1/3">CASH Invested (Down Pmt. + Closing Costs)</span><span></span><span></span><span class="v">$341.000</span></div>
    <div class="total"><span class="lead">Rate: 7%</span><span class="lead2">Term: 20 years</span><span class="tl">Monthly P&amp;I:</span><span class="tv">$10.482</span></div>

    <div class="sec cols"><span></span><span>DEPRICIATION (FIRST YEAR): (ASSUMES 80%/20%)</span><em>Est. Value</em><em>Yearly Rate</em><span></span></div>
    <div class="row"><span>Land Cost</span><span>0 Year</span><span>$338.000</span><span>0%</span><span class="v">$0</span></div>
    <div class="row"><span>Personal Property Cost</span><span>5 Years</span><span>$45.000</span><span>20%</span><span class="v">$9.000</span></div>
    <div class="row"><span>Building Cost</span><span>27.5 Years</span><span>$1.262.000</span><span>3.48%</span><span class="v">$43.918</span></div>
    <div class="row"><span>Land Improvement Cost</span><span>15 Years</span><span>$45.000</span><span>5%</span><span class="v">$2.250</span></div>
    <div class="total"><span class="tl">Total Depreciation:</span><span class="tv">$55.168</span></div>

    <div class="sec"><span class="sec-name">INCOME:</span></div>
    <div class="row"><span>Annual Rent</span><span></span><span></span><span></span><span class="v">$170.000</span></div>
    <div class="row"><span>Other Income</span><span></span><span></span><span></span><span class="v">$0</span></div>
    <div class="row"><span>Less Vacancy</span><span></span><span>est. 5% of annual rent</span><span></span><span class="v neg">-$0</span></div>
    <div class="total"><span class="tl">Gross Operating Income:</span><span class="tv">$170.000</span></div>

    <div class="sec"><span class="sec-name">EXPENSES:</span></div>
    <div class="row"><span>Real Estate Tax</span><span></span><span></span><span></span><span class="v">$27.439</span></div>
    <div class="row"><span>Insurance</span><span></span><span>est.</span><span></span><span class="v">$3.492</span></div>
    <div class="row"><span>Association Dues/HOA's</span><span></span><span></span><span></span><span class="v">$0</span></div>
    <div class="row"><span>Management</span><span></span><span>0%</span><span></span><span class="v">$0</span></div>
    <div class="row"><span>Utilities</span><span></span><span></span><span></span><span class="v">$9.192</span></div>
    <div class="sub">PROPERTY ADDRESS</div>
    <div class="row"><span>Advertising</span><span></span><span></span><span></span><span class="v">$170.000</span></div>
    <div class="row"><span>Maintenence</span><span></span><span>est.</span><span></span><span class="v">$40.123</span></div>
    <div class="row"><span>Miscellaneous1</span><span></span><span>est.</span><span></span><span class="v">$129.877</span></div>
    <div class="row"><span>Miscellaneous2</span><span></span><span>est.</span><span></span><span class="v">$125.784</span></div>
    <div class="total"><span class="tl">Total Expenses:</span><span class="tv">$4.092</span></div>
  </div>
  <div class="abs footer" style="left:16px;top:510px;width:337px"><span>418 Alder, REF #47v8487 by Northlake Realty | Report by Lena Ortiz PageForge at www.example-site.test. June 26th, 2023</span><span>Page 2/3</span></div>
</section>

<!-- PAGE 3 : benefits & returns -->
<section class="page page-3">
  <div class="abs logo-mark" style="left:19px;top:6px;width:31px;height:31px"></div>
  <div class="abs agency" style="left:59px;top:18px"><b>AGENCYNAME</b> <span>HERE</span></div>
  <div class="abs agent" style="right:90px;top:12px">
    <div class="agent-name">GREG <span>MILO</span></div>
    <div><svg viewBox="0 0 10 10"><path d="M2 1l2 2-1 1.3a6 6 0 0 0 2.7 2.7L7 6l2 2-1.3 1.4C4.5 9.6.4 5.5.6 2.3z" fill="none" stroke="#111" stroke-width="1"/></svg>(555) 014-2290</div>
    <div>greg@agency.test</div>
  </div>
  <div class="abs headshot" role="img" aria-label="Agent headshot" style="left:296px;top:13px;width:49px;height:53px"></div>
  <div class="abs rule" style="left:17px;top:48px;width:118px;background:var(--accent);height:1.3px"></div>
  <h2 class="abs prop-title" style="left:17px;top:52px">418 ALDER</h2>
  <div class="abs prop-sub" style="left:17px;top:65px">15-Plex of 1bd/1bth Apartments</div>
  <div class="abs prop-addr" style="left:17px;top:73px"><svg viewBox="0 0 8 10"><path d="M4 0a3.5 3.5 0 0 0-3.5 3.5C.5 6 4 10 4 10s3.5-4 3.5-6.5A3.5 3.5 0 0 0 4 0zm0 5a1.5 1.5 0 1 1 0-3 1.5 1.5 0 0 1 0 3z" fill="#111"/></svg>15-Plex of 1bd/1bth Apartments</div>

  <h2 class="abs section-title" style="left:17px;top:101px"><b>The Four</b> <span>Benefits</span></h2>
  <div class="abs panel" style="left:17px;top:115px;width:336px">
    <div class="sec"><span class="sec-name">CASH FLOW BEFOR TAX:</span></div>
    <div class="row"><span>Gross Operating Income</span><span></span><span></span><span></span><span class="v">$170.000</span></div>
    <div class="row"><span>Operating Expenses</span><span></span><span></span><span></span><span class="v">$40.123</span></div>
    <div class="row"><span>Net Operating Income</span><span></span><span></span><span></span><span class="v">$129.877</span></div>
    <div class="row"><span style="grid-column:1/3">Annual Debt Service (Monthly P&amp;I x 12)</span><span></span><span></span><span class="v">$125.784</span></div>
    <div class="total"><span class="tl">Chash flow befor tax:</span><span class="tv">$4.092</span></div>

    <div class="sec"><span class="sec-name">PRINCIPAL REDUCTION:</span></div>
    <div class="row"><span>Annual Debt Service</span><span></span><span></span><span></span><span class="v">$125.784</span></div>
    <div class="row"><span>Interest (first year)</span><span></span><span></span><span></span><span class="v neg">-$93.621</span></div>
    <div class="total"><span class="tl">Chash flow befor tax:</span><span class="tv">$32.163</span></div>

    <div class="sec"><span class="sec-name">TAXES PAID/SAVED:</span></div>
    <div class="row"><span>Net Operating Income</span><span></span><span></span><span></span><span class="v">$129.877</span></div>
    <div class="row"><span>Interest paid in first year</span><span></span><span></span><span></span><span class="v">$93.621</span></div>
    <div class="row"><span>Total Depreciation</span><span></span><span></span><span></span><span class="v">$55.168</span></div>
    <div class="row"><span>Taxable Income</span><span></span><span></span><span></span><span class="v neg">-$18.912</span></div>
    <div class="row"><span>Tax Bracket</span><span></span><span>28%</span><span></span><span class="v neg">-$5.295</span></div>
    <div class="total"><span class="tl">Taxes Saved:</span><span class="tv">$5.295</span></div>

    <div class="sec"><span class="sec-name">APPRECIATION:</span></div>
    <div class="total" style="margin-top:3px"><span class="tl">Estimate of Appriciation:</span><span class="tv">0%</span></div>
  </div>

  <h2 class="abs section-title" style="left:17px;top:333px"><b>Rates of</b> <span>Returns</span></h2>
  <div class="abs panel" style="left:17px;top:347px;width:336px">
    <div class="sec"><span class="sec-name">RETURN ON INVESTMENT WITHOUT APPRICIATION:</span></div>
    <div class="row"><span style="grid-column:1/4">Cash Flow before Tax + Principal Reduction + Tax Saved</span><span></span><span class="v">$30.961</span></div>
    <div class="row"><span>Cash Invested</span><span></span><span></span><span></span><span class="v">$341.000</span></div>
    <div class="total"><span class="tl">ROI w/o Appriciation</span><span class="tv">9.08%</span></div>

    <div class="sec"><span class="sec-name">CAPITALIZATION RATE:</span></div>
    <div class="row"><span>Net Operating Income</span><span></span><span></span><span></span><span class="v">$129.877</span></div>
    <div class="row"><span>Purchase Cost</span><span></span><span></span><span></span><span class="v">$1.690.000</span></div>
    <div class="total"><span class="tl">Capitalization Rate:</span><span class="tv">7.69%</span></div>

    <div class="sec"><span class="sec-name">CASH ON CASH:</span></div>
    <div class="row"><span>Cash Flow before Tax</span><span></span><span></span><span></span><span class="v">$4.092</span></div>
    <div class="row"><span>Cash Invested</span><span></span><span></span><span></span><span class="v">$341.000</span></div>
    <div class="total"><span class="tl">Cash On Cash:</span><span class="tv">1.2%</span></div>
  </div>
  <div class="abs footer" style="left:17px;top:513px;width:336px"><span>418 Alder, REF #47v8487 by Northlake Realty | Report by Lena Ortiz PageForge at www.example-site.test. June 26th, 2023</span><span>Page 3/3</span></div>
</section>

</body>
</html>
```